Unique Playing Card Deck Design

Brief:

I am looking for a designer to design a whole deck of cards from the ground up. I would like both the front and back designed for the deck, and would like the desk to include all the standard cards including jokers. I would like to make each card as unique as possible, so including original designs and artwork for the non-face cards as well.

I would like these cards to be poker size (63mm x 88mm, 2.5" x 3.5") or B8 size according to ISO 216) and I’ve attached a template that should be followed for the sizing.

No real limit on the design so be as creative as you can!

Design Details

Color Mode: RGB or CYMK for color images, Grayscale for black and white

File types: JPG, BMP, PNG, GIF, TIFF

Image resolution: Minimum 300 dpi

Bleeding: Allow 1/8" (approx 36 pixels based on a 300dpi image) for bleeding and a further 1/8" for safe area margin inside each side

EDIT: Because this project requires a lot of design work I am fine for the submissions to be limited to 3 or 4 cards that would demonstrate the overall direction that you are taking. Once I have chosen the designs we can continue refining them and adding the rest of the deck. I would also like a box for the cards to be designed and can provide a template after I have chosen the designers. Thanks and please let me know if you have any questions!

EDIT2: I realize this project is a lot of work and so I have taken the amounts that I had for 2nd and 3rd place and increased the reward for 1st place. I am still interested in selecting multiple designs, but because this project is being done on a committed payment basis I wanted to ensure that I was only obligated to select one design. However, if there are multiple designs that I am interested in, I will award the design work to an additional 1-3 designers (to a maximum of 4 total) on the same terms as 1st place. i.e. all designers selected will be paid the same amount. Thanks again for looking!

Target Market(s)

Adult card players who appreciate good design (i.e. the designs should not be cartoon-like or targeted at children). These are going to be premium cards printed on the best quality paper etc so I would like the design to reflect this.

Font styles to use
Decorative
Script

Requirements
Nice to have
• I will leave the design idea up to you but I like the look of really old playing cards (think of a deck of medieval playing cards for example). I also like the art deco kind of aesthetic. On the complete opposite side of the spectrum a very modern looking, minimalist design is also appealing.
• These are just a few ideas but as I said I am really open to anything. It just needs to be a bold, original design.

```html
<!DOCTYPE html>
<html lang="en">
<head>
<meta charset="utf-8">
<title>Ten of Diamonds</title>
<link rel="stylesheet" href="https://fonts.googleapis.com/css2?family=Libre+Baskerville:wght@700&display=swap">
<style>
  :root {
    --card-white: #ffffff;
    --felt-black: #161616;
    --diamond-red: #cf3027;
    --deco-yellow: #ffdd44;
    --rank-orange: #ee421d;
  }
  html, body {
    margin: 0;
    padding: 0;
    width: 815px;
    height: 1200px;
    overflow: hidden;
    background: var(--card-white);
  }
  .card {
    display: block;
    width: 815px;
    height: 1200px;
  }
  .card-stock { fill: var(--card-white); }
  .card-field { fill: var(--felt-black); }
  .suit-pip { fill: var(--diamond-red); }
  .deco-frame { fill: none; stroke: var(--deco-yellow); stroke-width: 4; }
  .deco-rule { fill: var(--deco-yellow); }
  .tile-red { fill: var(--diamond-red); }
  .tile-yellow { fill: var(--deco-yellow); }
  .tile-black { fill: var(--felt-black); }
  .rank-box { fill: var(--felt-black); stroke: var(--deco-yellow); stroke-width: 4; }
  .inset-frame { fill: none; stroke: var(--deco-yellow); stroke-width: 8; }
  .rank {
    font-family: "Libre Baskerville", "Times New Roman", serif;
    font-weight: 700;
    font-size: 118px;
    letter-spacing: -6px;
    fill: var(--rank-orange);
    text-anchor: middle;
  }
</style>
</head>
<body>
<svg class="card" viewBox="0 0 815 1200" xmlns="http://www.w3.org/2000/svg">
  <rect class="card-stock" x="0" y="0" width="815" height="1200" rx="28"/>
  <rect class="card-field" x="39" y="55" width="741" height="1089"/>

  <defs>
    <path id="diamond" d="M0,-55 Q14,-22 47,0 Q14,22 0,55 Q-14,22 -47,0 Q-14,-22 0,-55Z"/>
  </defs>
  <g class="corner-pips">
    <use href="#diamond" class="suit-pip" transform="translate(118 132)"/>
    <use href="#diamond" class="suit-pip" transform="translate(694 132)"/>
    <use href="#diamond" class="suit-pip" transform="translate(122 1068)"/>
    <use href="#diamond" class="suit-pip" transform="translate(694 1068)"/>
  </g>

  <path class="deco-frame" d="M190,124 H627 A80,80 0 0 0 707,204 V998 A80,80 0 0 0 627,1078 H190 A80,80 0 0 0 110,998 V204 A80,80 0 0 0 190,124 Z"/>

  <g class="side-rules">
    <rect class="deco-rule" x="77" y="310" width="6" height="476"/>
    <rect class="deco-rule" x="57" y="481" width="6" height="187"/>
    <rect class="deco-rule" x="729" y="321" width="6" height="476"/>
    <rect class="deco-rule" x="747" y="492" width="6" height="187"/>
  </g>

  <g class="tile-grid">
    <!-- row 1 -->
    <rect class="rank-box" x="152" y="241" width="156" height="138"/>
    <text class="rank" x="230" y="354">10</text>
    <g role="img" aria-label="Geometric star ornament in white line on red">
      <rect class="tile-red" x="310" y="241" width="185" height="138"/>
    </g>
    <rect class="tile-yellow" x="495" y="241" width="162" height="138"/>

    <!-- row 2 -->
    <rect class="tile-red" x="152" y="396" width="154" height="138"/>
    <rect class="tile-red" x="496" y="396" width="161" height="138"/>
    <rect class="rank-box" x="306" y="396" width="190" height="138"/>
    <text class="rank" x="401" y="509">10</text>

    <!-- row 3 -->
    <g role="img" aria-label="Art deco ornament of circles and ellipses in red on yellow">
      <rect class="tile-yellow" x="152" y="551" width="155" height="139"/>
    </g>
    <rect class="tile-red" x="307" y="551" width="188" height="139"/>
    <rect class="rank-box" x="495" y="551" width="162" height="139"/>
    <text class="rank" x="576" y="665">10</text>

    <!-- row 4 -->
    <rect class="rank-box" x="152" y="706" width="156" height="139"/>
    <text class="rank" x="230" y="820">10</text>
    <rect class="tile-yellow" x="308" y="706" width="187" height="139"/>
    <rect class="tile-red" x="495" y="706" width="162" height="139"/>
    <rect class="tile-black" x="507" y="719" width="138" height="115"/>
    <rect class="tile-red" x="524" y="734" width="104" height="83"/>
    <rect class="inset-frame" x="524" y="734" width="104" height="83"/>

    <!-- row 5 -->
    <rect class="tile-yellow" x="152" y="862" width="156" height="138"/>
    <rect class="tile-red" x="308" y="862" width="187" height="138"/>
    <rect class="rank-box" x="495" y="862" width="162" height="138"/>
    <text class="rank" x="576" y="975">10</text>
  </g>
</svg>
</body>
</html>
```